Flat bootstrap design for existing site

I'm looking for a modern flat design based around an existing logo. This has to be a custom design (no external templates), and implemented into a bootstrap framework.

The logo is attached as 2 versions - choose whichever you want, that flows better with whatever design you choose.

Added screenshots of the existing site (currently using the default bootstrap layouts). Please make your designs around those pages in the screenshots (i.e. the homepage only has the postal code input and the header). The active page has 3 screenshots, because I wanted to illustrate the other states that would be visible (in the table rows).

This is a moving/junk removal website, just for some context.

Here's some example websites (flat designs) that I like, just to give you an idea of what I'm after.

https://www.plimvora.com/
https://dacklow.com/
https://trevanu.com/
https://quobrintal.com/en/

Coding

Coded - Design and coding required

Number of Pages Required

5+ page

Colors

Designer to choose colors to be used in the design.

Requirements
Must have
• It must be a modern/simple flat design, that is built around the existing logo (attached).
• It has to be implemented using bootstrap.

```html
<!DOCTYPE html>
<html lang="en">
<head>
<meta charset="utf-8">
<title>Draymo – Booking Details</title>
<link href="https://fonts.googleapis.com/css2?family=Ubuntu:wght@400;500;700&display=swap" rel="stylesheet">
<style>
:root{
  --brand:#4bc8f4;
  --brand-dark:#29a9d9;
  --white:#ffffff;
  --panel:#f9f9f9;
  --text:#555555;
  --text-dark:#333333;
  --border:#8a8a8a;
  --table-border:#c8c8c8;
  --notice:#cfeaf4;
  --accepted:#72b35b;
  --accepted-edge:#5a9a46;
  --sent:#70c0e2;
  --sent-edge:#4ea6cc;
  --pending:#c2c2c2;
  --pending-edge:#a8a8a8;
}
*{box-sizing:border-box;margin:0;padding:0}
html,body{width:1200px;height:642px;overflow:hidden;background:var(--white);
  font-family:"Ubuntu",sans-serif;color:var(--text)}
.page{position:relative;width:1200px;height:642px}

.site-header{position:absolute;left:0;top:0;width:1200px;height:47px;background:var(--brand)}
.brand{position:absolute;left:99px;top:0;height:47px;display:flex;align-items:center;gap:7px;
  color:var(--white);font-weight:700;font-size:22px;letter-spacing:1px}
.brand-dot{width:12px;height:12px;border-radius:50%;background:var(--white)}
.main-nav{position:absolute;left:0;top:0;height:47px;width:1200px}
.nav-link{position:absolute;top:0;height:47px;line-height:47px;color:var(--white);
  font-size:13.5px;font-weight:500;text-decoration:none}
.nav-link.active{background:var(--brand-dark);text-align:center}
.nav-user svg{vertical-align:middle;margin-left:6px}

.booking-panel{position:absolute;left:185px;top:84px;width:830px;height:236px;
  background:var(--panel);border-radius:4px}
.panel-title{position:absolute;left:48px;top:24px;font-size:13.5px;font-weight:500;color:var(--text)}
.field-label{position:absolute;font-size:12px;color:var(--text)}
.field-input{position:absolute;height:24px;border:1px solid var(--border);background:var(--panel);
  font-size:8.5px;color:#777;padding:7px 13px;font-family:inherit}
.date-btn{position:absolute;right:-1px;top:-1px;width:30px;height:24px;background:var(--brand-dark);
  display:flex;align-items:center;justify-content:center}
.field-textarea{height:41px;padding:6px 4px}
.update-btn{position:absolute;left:38px;top:194px;width:140px;height:28px;border-radius:14px;
  background:var(--brand);border:1px solid var(--brand-dark);color:var(--white);
  font-family:inherit;font-weight:700;font-size:12.5px;letter-spacing:.5px}

.drivers-title{position:absolute;left:213px;top:350px;font-size:13.5px;font-weight:500}
.notice{position:absolute;left:206px;top:379px;width:787px;height:25px;background:var(--notice);
  font-size:8.5px;color:#666;padding:7px 28px}

.drivers-table{position:absolute;left:207px;top:423px;width:786px;height:162px;
  border:1px solid var(--table-border)}
.cell{position:absolute;font-size:9.5px;color:var(--text-dark)}
.cell.head{font-weight:500;font-size:9.5px}
.table-rule{position:absolute;left:0;top:28px;width:784px;height:1px;background:#e2e2e2}
.status{position:absolute;left:508px;width:108px;height:19px;font-size:9.5px;color:var(--white);
  text-align:center;line-height:17px;border:1px solid}
.status.accepted{background:var(--accepted);border-color:var(--accepted-edge)}
.status.sent{background:var(--sent);border-color:var(--sent-edge)}
.status.pending{background:var(--pending);border-color:var(--pending-edge)}

.site-footer{position:absolute;left:0;top:611px;width:1200px;height:31px;background:var(--brand);
  color:var(--white);font-size:11px;font-weight:500;text-align:center;line-height:31px}
</style>
</head>
<body>
<div class="page">
  <header class="site-header">
    <div class="brand"><span class="brand-dot"></span>DRAYMO</div>
    <nav class="main-nav">
      <a class="nav-link" style="left:634px" href="#">Book</a>
      <a class="nav-link" style="left:699px" href="#">How It Works</a>
      <a class="nav-link active" style="left:796px;width:136px" href="#">Become A Driver</a>
      <a class="nav-link nav-user" style="left:950px" href="#">alex@mailvento.com<svg width="8" height="5" viewBox="0 0 8 5"><path d="M0 0h8L4 5z" fill="#fff"/></svg></a>
    </nav>
  </header>

  <section class="booking-panel">
    <h2 class="panel-title">Booking Details</h2>
    <span class="field-label" style="left:47px;top:56px">Package Selected :</span>
    <div class="field-input" style="left:43px;top:80px;width:291px">Package 1</div>
    <span class="field-label" style="left:418px;top:56px">Pick-up time selected :</span>
    <div class="field-input" style="left:409px;top:80px;width:291px;padding-left:18px">July 18 at 4:13 am
      <span class="date-btn"><svg width="11" height="11" viewBox="0 0 11 11" fill="none" stroke="#fff" stroke-width="1"><rect x="0.5" y="1.5" width="10" height="9"/><path d="M0.5 4h10M3 0v3M8 0v3M3 6h1M5 6h1M7 6h1M3 8h1M5 8h1M7 8h1"/></svg></span>
    </div>
    <span class="field-label" style="left:47px;top:120px">Description :</span>
    <div class="field-input field-textarea" style="left:43px;top:141px;width:661px">1 large stove</div>
    <button class="update-btn">UPDATE</button>
  </section>

  <h2 class="drivers-title">Drivers In Your Area</h2>
  <p class="notice">Please stay on this page and be patient, while we contact the drivers and find you one ASAP</p>

  <div class="drivers-table">
    <span class="cell head" style="left:30px;top:9px">Name</span>
    <span class="cell head" style="left:180px;top:10px">Distance (km)</span>
    <span class="cell head" style="left:343px;top:9px">Agreed Pick-Up Time</span>
    <div class="table-rule"></div>

    <span class="cell" style="left:30px;top:39px">Ralph Dunmore</span>
    <span class="cell" style="left:180px;top:39px">4.04km away</span>
    <span class="cell" style="left:343px;top:39px">July 18 at 4:13 am</span>
    <span class="status accepted" style="top:35px">Time Accepted</span>
    <span class="cell" style="left:671px;top:40px">Payment Made</span>

    <span class="cell" style="left:30px;top:73px">Owen Fairley</span>
    <span class="cell" style="left:180px;top:73px">5.6km away</span>
    <span class="cell" style="left:343px;top:73px">-</span>
    <span class="status sent" style="top:69px">Request Sent</span>

    <span class="cell" style="left:30px;top:108px">Miles Harrow</span>
    <span class="cell" style="left:180px;top:108px">11.13km away</span>
    <span class="cell" style="left:343px;top:108px">-</span>
    <span class="status sent" style="top:104px">Request Sent</span>

    <span class="cell" style="left:30px;top:142px">Nate Calloway</span>
    <span class="cell" style="left:180px;top:142px">11.81km away</span>
    <span class="cell" style="left:343px;top:142px">-</span>
    <span class="status pending" style="top:138px">Pending</span>
  </div>

  <footer class="site-footer">© 2017 Draymo. All Rights Reserved.</footer>
</div>
</body>
</html>
```